Webdesign für Full-Service-Internetagentur
Zielgruppe
Falkenhainer Webdesign – Ihr Partner für außergewöhnliche Onlinepräsenzen
Wir bieten seit mehr als 16 Jahren Internetauftritte für kleine und mittelständische Unternehmen an.
Als Full-Service-Internetagentur liefern wir Ihnen individuelle auf Ihre Bedürfnisse, Ihre Branche und Ihre Zielgruppe zugeschnittene Lösungen für Ihre Onlinepräsentation an. Unser Angebot beinhaltet sowohl ein ideenreiches Webdesign kombiniert mit den aktuellsten Grundsätzen für Web-Programmierung als auch die Unterstützung für Ihr erfolgreiches Werben im Internet.
Eine gute Beratung heißt für uns genau hinhören und verstehen, was Sie wirklich brauchen. Je besser wir Ihre Ziele kennen, desto besser können wir Ihre Onlinepräsenz umsetzen. Unsere Kundenberater erläutern Ihnen persönlich mit Enthusiasmus die verschiedenen Möglichkeiten der Darstellung Ihrer Firma im Internet und entwickeln Konzepte, die Ihren Anforderungen bestmöglich entsprechen. Nicht nur während der Projektphase, sondern auch nach Onlinestellung Ihrer Internetseite stehen wir Ihnen mit persönlicher Kundenbetreuung und Supportdienstleistungen zur Verfügung.
Aufgabenstellung
siehe : https://www.falkenhainer-webdesign.example/

```html
<!DOCTYPE html>
<html lang="de">
<head>
<meta charset="utf-8">
<title>Falkenhainer Webdesign – Webdesign</title>
<link href="https://fonts.googleapis.com/css2?family=Poppins:wght@400;500;600&family=Open+Sans:wght@400;600&display=swap" rel="stylesheet">
<style>
:root{
  --red:#e3302f;
  --red-dark:#c52424;
  --ink:#1f1f1f;
  --muted:#9a9a9a;
  --line:#e6e6e6;
  --stage:#e4e4e4;
  --soft:#f6f5f7;
  --white:#fff;
  --photo-a:#c9b8ae;
  --photo-b:#8f8d93;
}
*{box-sizing:border-box;margin:0;padding:0}
html,body{width:1200px;height:4524px;overflow:hidden}
body{background:var(--stage);font-family:"Open Sans",sans-serif;color:var(--ink);position:relative}
h1,h2,h3,h4,.btn,.logo{font-family:"Poppins",sans-serif}
.abs{position:absolute}

/* brand card */
.brand-card{left:408px;top:40px;width:236px;height:84px;background:var(--white);display:flex;align-items:center;justify-content:center}
.brand-card .logo{font-size:16px;white-space:nowrap}

/* flat desktop preview */
.desk{left:205px;top:210px;width:620px;height:370px;background:var(--white);overflow:hidden}
.desk-head{height:60px;display:flex;align-items:center;justify-content:space-between;padding:0 24px;font-size:8px}
.desk-head nav{display:flex;gap:12px}
.desk-head nav span:first-child{color:var(--red)}
.desk-hero{height:200px;background:linear-gradient(120deg,var(--photo-a),var(--photo-b));position:relative}
.desk-hero .hero-card{left:90px;bottom:-10px;width:200px}
.desk-intro{display:flex;gap:30px;padding:30px 90px;font-size:7px;color:var(--muted)}
.desk-intro h3{font-size:12px;color:var(--ink);font-weight:500;width:180px;flex:none}

/* shared page */
.page{background:var(--white);overflow:hidden}
.logo{font-weight:500;color:var(--ink);line-height:1.15}
.head{display:flex;align-items:center;justify-content:space-between;padding:0 14px}
.phone-btn{background:var(--red);color:var(--white);font-size:10px;padding:7px 12px;display:flex;align-items:center;gap:6px;font-family:"Poppins",sans-serif;white-space:nowrap}
.burger{width:26px;height:24px;background:#e9e9e9;display:flex;flex-direction:column;justify-content:center;gap:3px;padding:0 6px;flex:none}
.burger i{display:block;height:2px;background:#888}
.photo{background:linear-gradient(125deg,var(--photo-a) 0%,#d8d2cf 45%,var(--photo-b) 100%);position:relative}
.hero-card{position:absolute;background:var(--white);padding:14px 18px}
.hero-card h1{font-size:20px;font-weight:600;line-height:1.05}
.btn{display:inline-block;font-size:8px;font-weight:600;letter-spacing:.5px;padding:7px 14px;text-transform:uppercase;white-space:nowrap}
.btn-red{background:var(--red);color:var(--white)}
.btn-line{border:1px solid rgba(255,255,255,.8);color:var(--white)}
.btn-grey{border:1px solid var(--line);color:var(--ink);background:var(--white)}
.badge{width:68px;height:66px;background:var(--red-dark);flex:none}
.badge::before{content:"";display:block;height:30px;background:#eee}
.kicker{font-size:8px;color:var(--red);font-weight:600;text-transform:uppercase;letter-spacing:.5px}
.p{font-size:9px;line-height:1.9;color:var(--muted)}
.rule{width:26px;height:2px;background:var(--red);margin-top:8px}
.card{background:var(--white);border:1px solid #f0eeee;text-align:center;padding:26px 20px}
.card svg{width:44px;height:44px}
.card h4{font-size:11px;font-weight:500;margin:10px 0 8px}
.card p{font-size:9px;line-height:1.7;color:var(--muted)}
.band{background:var(--red);color:var(--white);text-align:center}
.band h2{font-weight:500}
.slider{background:#ececec;position:relative}
.slider .shot{position:absolute;background:linear-gradient(160deg,#b9b4b3,#7d7373)}
.arrow{position:absolute;width:24px;height:24px;border-radius:50%;background:rgba(255,255,255,.4);top:50%}
.news-item h5{font-size:8px;font-weight:600;margin:6px 0}
.news-item .date{font-size:7px;color:var(--muted)}
.news-item .more{font-size:7px;color:var(--red)}
.field{border:1px solid var(--line);background:var(--white);height:26px;font-size:7px;color:var(--muted);padding:8px}
.foot h6{font-size:9px;color:var(--red);font-weight:600;text-transform:uppercase;margin-bottom:4px}
.foot{font-size:8px;line-height:1.6}

/* tablet page */
.tab{left:70px;top:905px;width:616px;height:2700px}
.tab .head{height:95px}
.tab .logo{font-size:14px}
.tab .hero{height:330px}
.tab .hero-card{left:140px;bottom:0;width:270px}
.tab .intro{padding:60px 14px 20px}
.tab .intro-top{display:flex;gap:14px;align-items:flex-start;padding-left:128px}
.tab .intro h2{font-size:19px;font-weight:500;line-height:1.3}
.tab .grid{display:grid;grid-template-columns:1fr 1fr;gap:20px;padding:20px 14px 50px;background:linear-gradient(#fff,#fbf4f4)}
.tab .card{height:192px}
.tab .band{height:154px;padding-top:34px}
.tab .band h2{font-size:21px;margin-bottom:18px}
.tab .refs{padding:36px 14px 20px;display:flex;justify-content:space-between;align-items:flex-end}
.tab .refs h2{font-size:20px;font-weight:500;line-height:1.2}
.tab .slider{height:330px;margin-top:10px}
.tab .news{padding:30px 14px}
.tab .news-head{display:flex;justify-content:space-between;align-items:center;margin-bottom:36px}
.tab .news-head h2{font-size:22px;font-weight:500}
.tab .news-cols{display:grid;grid-template-columns:repeat(3,1fr);gap:24px}
.tab .contact{background:var(--soft);padding:30px 14px;display:grid;grid-template-columns:350px 1fr;gap:24px}
.tab .contact h3{font-size:14px;font-weight:500;margin-bottom:18px}
.form-grid{display:grid;grid-template-columns:1fr 1fr;gap:10px 12px}
.tab .footer{padding:24px 14px}

/* mobile page */
.mob{left:830px;top:920px;width:288px;height:3520px}
.mob .head{height:90px;padding:0 8px;gap:6px}
.mob .logo{font-size:12px}
.mob .phone-btn{font-size:9px;padding:6px 9px}
.mob .hero{height:320px}
.mob .hero-card{left:0;right:0;bottom:0;padding:12px 8px;display:flex;justify-content:space-between}
.mob .hero-card h1{font-size:16px}
.mob .intro{padding:6px 8px 20px}
.mob .intro h2{font-size:10px;font-weight:600;margin-bottom:4px}
.mob .intro .p{font-size:7px;line-height:1.9}
.mob .stack{display:flex;flex-direction:column;gap:18px;padding:10px 14px 40px;background:linear-gradient(#fff,#fbf4f4)}
.mob .card{height:178px;padding-top:30px}
.mob .band{height:180px;padding-top:36px}
.mob .band h2{font-size:20px;line-height:1.35;margin-bottom:14px}
.mob .refs{padding:18px 14px}
.mob .refs h2{font-size:15px;font-weight:500;line-height:1.25}
.mob .slider{height:300px}
.mob .news{padding:20px 8px;text-align:left}
.mob .news-item{margin-top:26px}
.mob .contact{padding:20px 8px}
.mob .contact h3{font-size:14px;font-weight:500;margin-bottom:14px}
.mob .footer{background:var(--soft);padding:20px 8px}
</style>
</head>
<body>

<div class="abs brand-card"><span class="logo">Falkenhainer Webdesign</span></div>

<section class="abs desk">
  <div class="desk-head"><span class="logo" style="font-size:11px">Falkenhainer Webdesign</span><nav><span>Die Agentur</span><span>Referenzen</span><span>Angebote</span><span>Aktuelles</span><span>Kontakt</span><span>FAQ</span></nav></div>
  <div class="desk-hero" role="img" aria-label="Foto: Team arbeitet gemeinsam am Schreibtisch mit Bildschirm">
    <div class="hero-card abs"><h1 style="font-size:15px">Lasst uns beginnen Zusammenarbeiten</h1><span class="btn btn-red" style="margin-top:6px">Weiterlesen →</span></div>
  </div>
  <div class="desk-intro"><h3>Wir sind dynamisch Team von kreativen Menschen</h3><p>Wir bieten Web- und Entwicklungsservices für Startups und kleine Unternehmen, um einen Partner für Ihre Anforderungen zu finden.</p></div>
</section>

<!-- Tablet page -->
<section class="abs page tab">
  <header class="head"><span class="logo">Falkenhainer<br>Webdesign</span><span style="display:flex;gap:16px;align-items:center"><span class="phone-btn">☎ 0399 – 5550190</span><span class="burger"><i></i><i></i><i></i></span></span></header>
  <div class="photo hero" role="img" aria-label="Foto: Team bespricht Entwürfe am Schreibtisch">
    <div class="hero-card"><h1>Lasst uns beginnen Zusammenarbeiten</h1><span class="btn btn-red" style="margin-top:12px">Weiterlesen →</span></div>
  </div>
  <div class="intro">
    <div class="intro-top"><h2>Wir sind dynamisch Team von kreativen Menschender Innovation &amp; Entwicklungskompetenz.</h2><div class="badge" role="img" aria-label="Partnersiegel"></div></div>
    <p class="p" style="margin-top:14px">Wir bieten Web- und Entwicklungsservices für Startups und kleine Unternehmen, um einen Partner für Ihre Anforderungen in den Bereichen digitale Medien, Designentwicklung, Lead-Generierung und Kommunikation zu suchen. Wir arbeiten mit Ihnen, nicht für Sie. Obwohl wir große Ressourcen haben.</p>
    <p class="p" style="margin-top:8px">Wir haben unseren Hauptsitz in Deutschland, um einen Kunden bestmöglich bedienen zu können Basis, die sich weltweit erstreckt.</p>
  </div>
  <div class="grid">
    <div class="card"><svg viewBox="0 0 44 44" fill="none" stroke="#e3302f" stroke-width="1.5"><path d="M8 40V14l5-8 5 8v26zM26 6h10v34H26zM26 12h4M26 18h6M26 24h4M26 30h6M26 36h4"/></svg><h4>Konzeption &amp; Beratung</h4><p>Wir entwickeln Ihr individuelles Konzept und begleiten Sie über die Fertigstellung hinaus.</p></div>
    <div class="card"><svg viewBox="0 0 44 44" fill="none" stroke="#e3302f" stroke-width="1.5"><rect x="14" y="4" width="26" height="20"/><rect x="4" y="18" width="14" height="22"/><path d="M20 34h14M27 24v10M20 16l6-5 4 3 6-6"/></svg><h4>Webdesign &amp; Programmierung</h4><p>Wir setzen Ihre individuell gestaltete Webseite mittels aktueller Web-Technologien um.</p></div>
    <div class="card"><svg viewBox="0 0 44 44" fill="none" stroke="#e3302f" stroke-width="1.5"><circle cx="22" cy="22" r="17"/><path d="M12 30l8-8 5 5 9-10M28 17h6v6"/></svg><h4>Online Marketing</h4><p>Wir analysieren Ihre Webseite und schaffen Voraussetzungen für ein optimales Suchmaschinen-Ranking.</p></div>
    <div class="card"><svg viewBox="0 0 44 44" fill="none" stroke="#e3302f" stroke-width="1.5"><rect x="6" y="6" width="32" height="32"/><path d="M6 13h32"/><text x="13" y="31" font-size="11" fill="#e3302f" stroke="none" font-family="Poppins,sans-serif">.de</text></svg><h4>Domain &amp; Webhosting</h4><p>Alles was Sie für Ihr Webprojekt brauchen.</p></div>
  </div>
  <div class="band"><h2>Ehrlich. Streßerprobt. Verständlich. Erfolgreich.</h2><span class="btn btn-line">Angebot einholen →</span></div>
  <div class="refs"><div><div class="kicker">Referenzen</div><h2>Wir haben viel Arbeit geleistet Überprüfen<br>Sie einige von hier</h2><div class="rule"></div></div><span class="btn btn-grey">Siehe alle Projekte</span></div>
  <div class="slider" role="img" aria-label="Referenzprojekt auf verschiedenen Geräten">
    <span class="shot" style="left:136px;top:50px;width:300px;height:150px"></span>
    <span class="shot" style="left:70px;top:150px;width:96px;height:62px"></span>
    <span class="shot" style="left:400px;top:160px;width:120px;height:78px"></span>
    <span class="shot" style="left:40px;top:190px;width:34px;height:58px"></span>
    <span class="arrow" style="left:22px"></span><span class="arrow" style="right:22px"></span>
  </div>
  <div class="news">
    <div class="news-head"><div><div class="kicker" style="color:var(--muted)">Nachrichten</div><h2>Was es neues gibt</h2></div><span class="btn btn-grey" style="background:#eee">Alle Nachrichten anzeigen</span></div>
    <div class="news-cols">
      <div class="news-item"><div class="date">May 10, 2019</div><h5>"Für jeden" ETWAS bei Falkenhainer Webdesign</h5><p class="date">Falkenhainer Webdesign kann einen weiteren neuen Kunden begrüßen!</p><p class="more">Weiterlesen</p></div>
      <div class="news-item"><div class="date">Juli 108, 2019</div><h5>Malerprojekt Falkenhain GmbH</h5><p class="date">Neue Website für die Malerprojekt Falkenhain GmbH</p><p class="more">Weiterlesen</p></div>
      <div class="news-item"><div class="date">Januar 15, 2019</div><h5>ACHTUNG – eingeschränkte Verfügbarkeit von HostedExchange-Konten</h5><p class="date">Aktuelle Systemmeldungen Hostwerk</p><p class="more">Weiterlesen</p></div>
    </div>
  </div>
  <div class="contact">
    <div><h3>Wir haben Ihr Interesse geweckt?</h3>
      <div class="form-grid"><div class="field">Name *</div><div class="field">Firma</div><div class="field">Straße, Nr</div><div class="field">PLZ, Ort</div><div class="field">Telefon *</div><div class="field">E-Mail *</div><div class="field" style="grid-column:span 2;height:74px">Ihre Nachricht an uns *</div></div>
      <p class="p" style="font-size:7px;line-height:1.6;margin:20px 0 12px 24px;color:#555">Ich habe die Datenschutzerklärung zur Kenntnis genommen. Ich stimme zu, dass meine Angaben zur Beantwortung meiner Anfrage erhoben und gespeichert werden. Die Einwilligung kann jederzeit per E-Mail an <span style="color:var(--red)">info@falkenhainer-webdesign.example</span> widerrufen werden.</p>
      <span class="btn btn-red" style="border-radius:12px">Formular abschicken</span>
    </div>
    <div><div class="kicker" style="color:var(--muted)">Kontaktiere uns</div><h3 style="font-size:12px;margin:10px 0">Zögern Sie nicht Kontaktieren Sie uns für alle Art von Informationen</h3><p class="p" style="font-size:8px;line-height:1.5">Rufen Sie uns zur sofortigen Unterstützung diese Nummer an</p><p style="font-weight:600;font-size:12px;margin-top:6px">0399 – 5550190</p></div>
  </div>
  <footer class="footer foot" style="display:grid;grid-template-columns:1fr 1fr 1fr;gap:10px">
    <div><h6>Navigation</h6><div style="display:grid;grid-template-columns:1fr 1fr">Portfolio<span>Kontakt</span>Die Agentur<span>FAQ</span>Referenzen<span>Impressum</span>Aktuelles<span>Datenschutz</span></div></div>
    <div><h6>Kontakt</h6>Falkenhainer Webdesign<br>Inh. Lena Brandt<br>Lindenweg 12<br>09100 Falkenhain</div>
    <div style="padding-top:14px">Fon: 0399 - 5550190<br>Fax: 0399 - 5550191<br><span style="color:var(--red)">info@falkenhainer-webdesign.example</span></div>
    <div style="grid-column:span 3;margin-top:24px">© 2019 by <span style="color:var(--red)">Falkenhainer Webdesign</span></div>
  </footer>
</section>

<!-- Mobile page -->
<section class="abs page mob">
  <header class="head"><span class="logo">Falkenhainer<br>Webdesign</span><span class="phone-btn">☎ 0399 – 5550190</span><span class="burger"><i></i><i></i><i></i></span></header>
  <div class="photo hero" role="img" aria-label="Foto: Team bespricht Entwürfe am Schreibtisch">
    <div class="hero-card"><div><h1>Lasst uns beginnen Zusammenarbeiten</h1><span class="btn btn-red" style="margin-top:10px">Weiterlesen →</span></div><div class="badge" style="width:60px;height:60px" role="img" aria-label="Partnersiegel"></div></div>
  </div>
  <div class="intro"><h2>Wir sind dynamisch Team von kreativen Menschender Innovation &amp; Entwicklungskompetenz.</h2>
    <p class="p">Wir bieten Web- und Entwicklungsservices für Startups und kleine Unternehmen, um einen Partner für Ihre Anforderungen in den Bereichen digitale Medien, Designentwicklung, Lead-Generierung und Kommunikation zu suchen. Wir arbeiten mit Ihnen, nicht für Sie. Obwohl wir große Ressourcen haben. Wir haben unseren Hauptsitz in Deutschland, um einen Kunden bestmöglich bedienen zu können Basis, die sich weltweit erstreckt.</p></div>
  <div class="stack">
    <div class="card"><svg viewBox="0 0 44 44" fill="none" stroke="#e3302f" stroke-width="1.5"><path d="M8 40V14l5-8 5 8v26zM26 6h10v34H26zM26 12h4M26 18h6M26 24h4M26 30h6M26 36h4"/></svg><h4>Konzeption &amp; Beratung</h4><p>Wir entwickeln Ihr individuelles Konzept und begleiten Sie über die Fertigstellung hinaus.</p></div>
    <div class="card"><svg viewBox="0 0 44 44" fill="none" stroke="#e3302f" stroke-width="1.5"><rect x="14" y="4" width="26" height="20"/><rect x="4" y="18" width="14" height="22"/><path d="M20 34h14M27 24v10M20 16l6-5 4 3 6-6"/></svg><h4>Webdesign &amp; Programmierung</h4><p>Wir setzen Ihre individuell gestaltete Webseite mittels aktueller Web-Technologien um.</p></div>
    <div class="card"><svg viewBox="0 0 44 44" fill="none" stroke="#e3302f" stroke-width="1.5"><circle cx="22" cy="22" r="17"/><path d="M12 30l8-8 5 5 9-10M28 17h6v6"/></svg><h4>Online Marketing</h4><p>Wir analysieren Ihre Webseite und schaffen Voraussetzungen für ein optimales Suchmaschinen-Ranking.</p></div>
    <div class="card"><svg viewBox="0 0 44 44" fill="none" stroke="#e3302f" stroke-width="1.5"><rect x="6" y="6" width="32" height="32"/><path d="M6 13h32"/><text x="13" y="31" font-size="11" fill="#e3302f" stroke="none" font-family="Poppins,sans-serif">.de</text></svg><h4>Domain &amp; Webhosting</h4><p>Alles was Sie für Ihr Webprojekt brauchen.</p></div>
  </div>
  <div class="band"><h2>Ehrlich. Streßerprobt.<br>Verständlich. Erfolgreich.</h2><span class="btn btn-line">Angebot einholen →</span></div>
  <div class="refs"><div class="kicker">Referenzen</div><h2>Wir haben viel Arbeit geleistet Überprüfen Sie einige von hier</h2><div style="display:flex;justify-content:space-between;align-items:center"><div class="rule"></div><span class="btn btn-grey" style="margin-right:40px">Siehe alle Projekte</span></div></div>
  <div class="slider" role="img" aria-label="Referenzprojekt auf verschiedenen Geräten">
    <span class="shot" style="left:20px;top:60px;width:250px;height:130px"></span>
    <span class="shot" style="left:10px;top:170px;width:40px;height:64px"></span>
    <span class="shot" style="left:50px;top:180px;width:70px;height:48px"></span>
    <span class="shot" style="left:180px;top:180px;width:94px;height:60px"></span>
  </div>
  <div class="news">
    <div style="text-align:center"><div class="kicker" style="color:var(--muted)">Nachrichten</div><h2 style="font-size:15px;font-weight:500;margin:4px 0 14px">Was es neues gibt</h2><span class="btn btn-grey" style="background:#eee">Alle Nachrichten anzeigen</span></div>
    <div class="news-item"><div class="date">May 10, 2019</div><h5>"Für jeden" ETWAS bei Falkenhainer Webdesign</h5><p class="date">Falkenhainer Webdesign kann einen weiteren neuen Kunden begrüßen!</p><p class="more">Weiterlesen</p></div>
    <div class="news-item"><div class="date">Juli 108, 2019</div><h5>Malerprojekt Falkenhain GmbH</h5><p class="date">Neue Website für die Malerprojekt Falkenhain GmbH</p><p class="more">Weiterlesen</p></div>
    <div class="news-item"><div class="date">Januar 15, 2019</div><h5>ACHTUNG – eingeschränkte Verfügbarkeit von HostedExchange-Konten</h5><p class="date">Aktuelle Systemmeldungen Hostwerk</p><p class="more">Weiterlesen</p></div>
  </div>
  <div class="contact">
    <h3>Wir haben Ihr Interesse geweckt?</h3>
    <div class="form-grid"><div class="field">Name *</div><div class="field">Firma</div><div class="field">Straße, Nr</div><div class="field">PLZ, Ort</div><div class="field">Telefon *</div><div class="field">E-Mail *</div><div class="field" style="grid-column:span 2;height:80px">Ihre Nachricht an uns *</div></div>
    <p class="p" style="font-size:6.5px;line-height:1.6;margin:26px 0 14px 24px;color:#555">Ich habe die Datenschutzerklärung zur Kenntnis genommen. Ich stimme zu, dass meine Angaben zur Beantwortung meiner Anfrage erhoben und gespeichert werden. Widerruf per E-Mail an <span style="color:var(--red)">info@falkenhainer-webdesign.example</span> möglich.</p>
    <span class="btn btn-red" style="border-radius:12px">Formular abschicken</span>
    <div class="kicker" style="color:var(--muted);margin-top:46px">Kontaktiere uns</div>
    <h3 style="font-size:12px;margin:6px 0 8px">Zögern Sie nicht Kontaktieren Sie uns für alle Art von Informationen</h3><div class="rule"></div>
    <p class="p" style="font-size:7px;margin-top:16px">Rufen Sie uns zur sofortigen Unterstützung diese Nummer an</p>
    <p style="font-weight:600;font-size:12px;margin-top:4px">0399 – 5550190</p>
  </div>
  <footer class="footer foot">
    <h6>Navigation</h6><div style="display:grid;grid-template-columns:1fr 1fr">Portfolio<span>Kontakt</span>Die Agentur<span>FAQ</span>Referenzen<span>Impressum</span>Aktuelles<span>Datenschutz</span></div>
    <h6 style="margin-top:18px">Kontakt</h6>
    <div style="display:grid;grid-template-columns:1fr 1fr;gap:6px"><div>Falkenhainer Webdesign<br>Inh. Lena Brandt<br>Lindenweg 12<br>09100 Falkenhain</div><div>Fon: 0399 - 5550190<br>Fax: 0399 - 5550191<br><span style="color:var(--red);font-size:7px;word-break:break-all">info@falkenhainer-webdesign.example</span></div></div>
    <div style="margin-top:50px">© 2019 by <span style="color:var(--red)">Falkenhainer Webdesign</span></div>
  </footer>
</section>

</body>
</html>
```